Ductless Mini Split Business Website

Copper Fern Services is looking to design an eye catching educational website about installing Ductless mini splits.

Similar to this company.
https://www.halvikstream.com/

Coding

Coded - Design and coding required

```html
<!DOCTYPE html>
<html lang="en">
<head>
<meta charset="utf-8">
<title>Copper Fern Services — Ductless Experts</title>
<link href="https://fonts.googleapis.com/css2?family=Cinzel:wght@400;700&family=Lato:ital,wght@0,400;0,700;0,900;1,400&display=swap" rel="stylesheet">
<style>
:root{
  --yellow:#fdd20b;
  --yellow-dark:#c9a300;
  --dark:#161616;
  --text:#222;
  --muted:#666;
  --white:#fff;
  --line:#d9d9d9;
}
*{box-sizing:border-box;margin:0;padding:0}
html,body{width:1200px;height:4463px;overflow:hidden}
body{position:relative;font-family:"Lato",sans-serif;color:var(--text);background:var(--white)}
h1,h2,h3,h4,h5{font-weight:400}
.abs{position:absolute}
.btn{position:absolute;display:flex;align-items:center;justify-content:center;background:var(--yellow);color:#222;border-radius:30px;font-family:"Cinzel",serif}

/* top bar */
.topbar{top:0;left:0;width:1200px;height:35px;background:var(--yellow);font-size:14px}
.topbar .addr{position:absolute;left:92px;top:9px;display:flex;gap:8px;align-items:center}
.social{display:flex;gap:7px}
.social span{width:16px;height:16px;background:#222;border-radius:3px;display:block}
.topbar .social{position:absolute;right:90px;top:9px}

/* header */
.header{top:35px;left:0;width:1200px;height:103px;background:var(--white)}
.brand{position:absolute;left:92px;top:16px;display:flex;align-items:center;gap:10px}
.brand .dot{width:26px;height:26px;border-radius:50%;background:var(--yellow)}
.brand .name{font-family:"Cinzel",serif;font-weight:700;font-size:17px;color:#222;line-height:1.15}
.header .tag{position:absolute;left:97px;top:76px;font-weight:700;font-size:16px;letter-spacing:.5px;color:#222}
.nav{position:absolute;right:90px;top:38px;display:flex;gap:53px;font-family:"Cinzel",serif;font-size:18px}
.nav a{color:#222;text-decoration:none}
.nav a.active{color:var(--yellow-dark)}

/* hero */
.hero{top:138px;left:0;width:1200px;height:581px;background:linear-gradient(100deg,#5d4a3a 0%,#8a7563 30%,#a89584 55%,#6f6157 80%,#4c3f37 100%)}
.hero::after{content:"";position:absolute;inset:0;background:rgba(0,0,0,.18)}
.hero .in{position:absolute;inset:0;z-index:1;text-align:center;color:var(--white)}
.hero h1{position:absolute;top:180px;width:100%;font-family:"Cinzel",serif;font-size:60px;letter-spacing:1px}
.hero p{position:absolute;top:258px;width:100%;font-size:18px;line-height:27px}
.hero .btn{left:481px;top:326px;width:210px;height:56px;font-size:22px}

/* welcome */
.welcome h2{top:815px;width:1200px;text-align:center;font-family:"Cinzel",serif;font-size:35px;color:#111}
.welcome p{top:884px;left:140px;width:920px;text-align:center;font-size:16.5px;line-height:32px;color:var(--muted)}
.welcome .btn{left:495px;top:1048px;width:208px;height:55px;font-size:21px}

/* dark sections */
.dark{left:0;width:1200px;background:linear-gradient(90deg,#111 0%,#1d1d1d 50%,#141414 100%)}
.services-band{top:1212px;height:567px}
.about-band{top:2416px;height:506px}
.cut{position:absolute;display:block}
.sec-title{font-family:"Cinzel",serif;font-weight:700;color:var(--yellow);font-size:36px}
.services-band .sec-title{position:absolute;left:87px;top:115px}
.services-band .intro{position:absolute;left:90px;top:172px;width:282px;color:#eee;font-size:14.5px;line-height:32px;text-align:justify}
.services-band .btn{left:87px;top:398px;width:164px;height:44px;font-family:"Lato",sans-serif;font-size:16px;letter-spacing:.5px}
.card{position:absolute;top:125px;width:217px;height:317px;background:var(--white);text-align:center}
.card .icon{position:absolute;left:70px;top:28px;width:78px;height:78px;border-radius:50%;background:var(--yellow)}
.card h3{position:absolute;top:124px;width:100%;font-family:"Cinzel",serif;font-size:22px;line-height:27px;color:#111}
.card p{position:absolute;top:190px;left:10px;width:197px;font-size:11px;line-height:21px;color:#555}
.card .go{position:absolute;right:0;bottom:0;width:35px;height:21px;background:var(--yellow);display:flex;align-items:center;justify-content:center}

/* why */
.why-photo{left:0;top:1883px;width:559px;height:429px;background:linear-gradient(135deg,#e9ecef 0%,#cfd4d8 45%,#8f9aa3 75%,#5e6a74 100%)}
.why h2{left:646px;top:1874px;font-family:"Cinzel",serif;font-size:36px;line-height:47px;color:#111}
.feat{position:absolute;left:641px;width:470px}
.feat .ic{position:absolute;left:0;top:0;width:46px;height:46px;border-radius:50%;background:var(--yellow);box-shadow:0 3px 6px rgba(0,0,0,.15)}
.feat h4{position:absolute;left:63px;top:6px;font-family:"Cinzel",serif;font-size:22px;color:#111;white-space:nowrap}
.feat p{position:absolute;left:63px;top:48px;width:420px;font-size:14.5px;line-height:27px;color:#444}

/* about */
.about-band .sec-title{position:absolute;left:92px;top:84px}
.about-band .intro{position:absolute;left:90px;top:145px;width:484px;color:#eee;font-size:14.5px;line-height:32px;text-align:justify}
.about-band .btn{left:90px;top:390px;width:163px;height:43px;font-family:"Lato",sans-serif;font-size:16px}
.about-photo{position:absolute;left:694px;top:90px;width:416px;height:343px;border:4px solid var(--white);background:linear-gradient(120deg,#f2f3f4 0%,#d7dde2 40%,#3c7fc4 70%,#1f5fa8 100%)}

/* testimonials */
.t-kicker{top:3028px;width:1200px;text-align:center;font-family:"Cinzel",serif;font-size:17px;color:#222}
.t-title{top:3054px;width:1200px;text-align:center;font-family:"Cinzel",serif;font-size:36px;color:#111}
.avatar{left:528px;top:3119px;width:144px;height:144px;border-radius:50%;border:5px solid var(--yellow);background:radial-gradient(circle at 50% 45%,#b88a68 0%,#7a5640 55%,#e8e2da 100%)}
.quote{top:3271px;left:200px;width:800px;text-align:center;font-style:italic;font-size:19px;line-height:38px;color:#666;white-space:nowrap}
.qmark{display:block}
.t-name{top:3410px;width:1200px;text-align:center;font-family:"Cinzel",serif;font-size:26px;color:#111}
.dots{top:3465px;left:574px;display:flex;gap:8px}
.dots span{width:14px;height:14px;border-radius:50%;border:2px solid #222;display:block}
.dots span.on{background:#222}

/* map & contact */
.map{top:3528px;left:0;width:1200px;height:485px;background:linear-gradient(160deg,#f1f1f1 0%,#e6e6e6 50%,#eeeeee 100%)}
.contact{left:90px;top:3692px;width:488px;height:435px;background:var(--white);box-shadow:0 4px 20px rgba(0,0,0,.12);z-index:2}
.contact h2{position:absolute;left:36px;top:48px;font-family:"Cinzel",serif;font-size:35px;color:#111}
.field{position:absolute;left:36px;width:376px;border-bottom:1px solid var(--line);font-size:13px;color:#222;padding-bottom:14px}
.contact .btn{left:35px;top:343px;width:163px;height:40px;font-size:15px}

/* footer */
.footer{top:4013px;left:0;width:1200px;height:450px;background:var(--dark)}
.footer .brand{left:90px;top:166px}
.footer .brand .name{color:var(--yellow)}
.footer .tagline{position:absolute;left:90px;top:222px;font-weight:700;font-size:18px;color:var(--yellow)}
.footer .about-text{position:absolute;left:90px;top:255px;width:232px;color:#eee;font-size:13.5px;line-height:24px;text-align:justify}
.footer .social{position:absolute;left:90px;top:364px;gap:12px}
.footer .social span{width:20px;height:20px;background:#eee}
.fcol{position:absolute;top:178px;color:#eee}
.fcol h5{font-family:"Cinzel",serif;font-size:21px;margin-bottom:14px}
.fcol li{list-style:none;font-size:14.5px;line-height:27px}
.copy{position:absolute;top:410px;width:100%;text-align:center;color:#eee;font-size:14.5px}
.copy span{margin:0 14px}
</style>
</head>
<body>

<div class="abs topbar">
  <div class="addr">
    <svg width="12" height="16" viewBox="0 0 12 16"><path d="M6 0C2.7 0 0 2.6 0 5.9 0 10 6 16 6 16s6-6 6-10.1C12 2.6 9.3 0 6 0zm0 8.3a2.4 2.4 0 1 1 0-4.8 2.4 2.4 0 0 1 0 4.8z" fill="#222"/></svg>
    418 Larkspur Ave. Chicago, IL 60619
  </div>
  <div class="social"><span></span><span></span><span></span><span></span></div>
</div>

<header class="abs header">
  <div class="brand">
    <span class="dot"></span>
    <span class="name">Copper Fern<br>Services</span>
  </div>
  <span class="tag">DUCTLESS EXPERTS</span>
  <nav class="nav">
    <a class="active" href="#">Home</a><a href="#">About Us</a><a href="#">Services</a><a href="#">Faq</a><a href="#">Review</a><a href="#">Contact Us</a>
  </nav>
</header>

<section class="abs hero" role="img" aria-label="Man relaxing on a sofa in a living room with a wall-mounted ductless unit">
  <div class="in">
    <h1>COPPER FERN SERVICES</h1>
    <p>Ut enim ad minim veniam, quis nostrud exercitation ullamco<br>laboris nisi ut aliquip ex ea commodo consequat.</p>
    <span class="btn">GET A QUOTE</span>
  </div>
</section>

<section class="welcome">
  <h2 class="abs">WELCOME TO COPPER FERN SERVICES</h2>
  <p class="abs">Lorem ipsum dolor sit amet, consectetur adipiscing elit, sed do eiusmod tempor incididunt ut labore et dolore magna aliqua. Ut enim ad minim veniam, quis nostrud exercitation ullamco laboris nisi ut aliquip ex ea commodo consequat. Duis aute irure dolor in reprehenderit in voluptate velit esse cillum dolore eu fugiat nulla pariatur.Excepteur sint occaecat cupidatat non proident, sunt in culpa qui officia deserunt mollit anim id est laborum</p>
  <span class="btn">READ MORE</span>
</section>

<section class="abs dark services-band" aria-label="Services">
  <svg class="cut" style="left:0;top:0" width="125" height="78"><polygon points="0,0 125,0 0,78" fill="#fff"/></svg>
  <svg class="cut" style="right:0;bottom:0" width="126" height="82"><polygon points="126,0 126,82 0,82" fill="#fff"/></svg>
  <h2 class="sec-title">SERVICES</h2>
  <p class="intro">Lorem ipsum dolor sit amet, consectetur adipiscing elit, sed do eiusmod tempor incididunt ut labore et dolore magna aliqua. Ut enim ad minim veniam, quis nostrud exercitation ullamco laboris nisi ut aliquip ex ea commodo consequat.</p>
  <span class="btn">SHOW DETAILS</span>

  <div class="card" style="left:412px">
    <div class="icon"><svg width="78" height="78"><rect x="19" y="26" width="40" height="18" rx="3" fill="none" stroke="#222" stroke-width="3"/><line x1="24" y1="37" x2="54" y2="37" stroke="#222" stroke-width="2"/><path d="M28 48v6M34 48v6M40 48v6M46 48v6M52 48v6" stroke="#222" stroke-width="2"/></svg></div>
    <h3>DUCTLESS<br>INSTALLATION</h3>
    <p>Lorem ipsum dolor sit amet, consectetur adipiscing elit, sed do eiusmod tempor incididunt ut labore et dolore magna aliqua.</p>
    <span class="go"><svg width="16" height="10"><path d="M0 5h13M9 1l4 4-4 4" stroke="#222" stroke-width="2" fill="none"/></svg></span>
  </div>
  <div class="card" style="left:653px">
    <div class="icon"><svg width="78" height="78"><path d="M39 17l18 7v13c0 12-8 19-18 23-10-4-18-11-18-23V24z" fill="none" stroke="#222" stroke-width="3"/><path d="M31 39l6 6 11-12" fill="none" stroke="#222" stroke-width="3"/></svg></div>
    <h3>DUCTLESS<br>WARRANTY</h3>
    <p>Lorem ipsum dolor sit amet, consectetur adipiscing elit, sed do eiusmod tempor incididunt ut labore et dolore magna aliqua.</p>
    <span class="go"><svg width="16" height="10"><path d="M0 5h13M9 1l4 4-4 4" stroke="#222" stroke-width="2" fill="none"/></svg></span>
  </div>
  <div class="card" style="left:894px">
    <div class="icon"><svg width="78" height="78"><circle cx="42" cy="46" r="14" fill="none" stroke="#222" stroke-width="3"/><path d="M42 32v-8M36 24h12M20 26h12M26 20l6 6-6 6" stroke="#222" stroke-width="3" fill="none"/></svg></div>
    <h3>DUCTLESS<br>HEAT PUMP</h3>
    <p>Lorem ipsum dolor sit amet, consectetur adipiscing elit, sed do eiusmod tempor incididunt ut labore et dolore magna aliqua.</p>
    <span class="go"><svg width="16" height="10"><path d="M0 5h13M9 1l4 4-4 4" stroke="#222" stroke-width="2" fill="none"/></svg></span>
  </div>
</section>

<section class="why">
  <div class="abs why-photo" role="img" aria-label="Technician in blue gloves servicing an open indoor ductless unit"></div>
  <h2 class="abs">WHY CHOOSE<br>COPPER FERN SERVICES?</h2>
  <div class="feat" style="top:1988px"><span class="ic"></span><h4>0% FINANCING FOR 60 MONTHS</h4><p>Lorem ipsum dolor sit amet, consectetur adipiscing elit, sed do eiusmod tempor incididunt ut labore et dolore</p></div>
  <div class="feat" style="top:2100px"><span class="ic"></span><h4>MONEY BACK GUARANTEE</h4><p>Lorem ipsum dolor sit amet, consectetur adipiscing elit, sed do eiusmod tempor incididunt ut labore et dolore</p></div>
  <div class="feat" style="top:2215px"><span class="ic"></span><h4>EXPERTS IN DUCTLESS SERVICES</h4><p>Lorem ipsum dolor sit amet, consectetur adipiscing elit, sed do eiusmod tempor incididunt ut labore et dolore</p></div>
</section>

<section class="abs dark about-band" aria-label="About us">
  <svg class="cut" style="left:0;top:0" width="121" height="78"><polygon points="0,0 121,0 0,78" fill="#fff"/></svg>
  <svg class="cut" style="right:0;bottom:0" width="112" height="99"><polygon points="112,0 112,99 0,99" fill="#fff"/></svg>
  <h2 class="sec-title">ABOUT US</h2>
  <p class="intro">Lorem ipsum dolor sit amet, consectetur adipiscing elit, sed do eiusmod tempor incididunt ut labore et dolore magna aliqua. Ut enim ad minim veniam, quis nostrud exercitation ullamco laboris nisi ut aliquip ex ea commodo consequat. Duis aute irure dolor in reprehenderit in voluptate velit esse cillum dolore eu fugiat nulla pariaturExcepteur sint occaecat cupidatat non proident, sunt in culpa qui officia deserunt mollit anim id est laborum</p>
  <span class="btn">READ MORE</span>
  <div class="about-photo" role="img" aria-label="Technician in a blue cap repairing a wall-mounted ductless unit"></div>
</section>

<section class="testimonials">
  <p class="abs t-kicker">WHAT OUR PEOPLE SAYS</p>
  <h2 class="abs t-title">TESTIMONIALS</h2>
  <div class="abs avatar" role="img" aria-label="Customer portrait"></div>
  <svg class="abs qmark" style="left:152px;top:3263px" width="46" height="38" viewBox="0 0 46 38" aria-hidden="true">
    <path d="M0 38V22C0 10 6 3 17 0l2 5C13 8 10 12 10 17h9v21zM27 38V22C27 10 33 3 44 0l2 5c-6 3-9 7-9 12h9v21z" fill="#fde68a"/>
  </svg>
  <p class="abs quote">Lorem ipsum dolor sit amet, consectetur adipiscing elit, sed do eiusmod tempor incididunt ut<br>labore et dolore magna aliqua. Ut enim ad minim veniam, quis nostrud exercitation ullamco<br>laboris nisi ut aliquip ex ea commodo consequat.</p>
  <svg class="abs qmark" style="left:829px;top:3364px" width="46" height="38" viewBox="0 0 46 38" aria-hidden="true">
    <path d="M46 0v16c0 12-6 19-17 22l-2-5c6-3 9-7 9-12h-9V0zM19 0v16C19 28 13 35 2 38L0 33c6-3 9-7 9-12H0V0z" fill="#fde68a"/>
  </svg>
  <p class="abs t-name">MARCUS</p>
  <div class="abs dots"><span></span><span class="on"></span><span></span></div>
</section>

<div class="abs map" role="img" aria-label="Street map of the service area"></div>
<form class="abs contact">
  <h2>GET IN TOUCH</h2>
  <div class="field" style="top:116px">Name</div>
  <div class="field" style="top:188px">Email address</div>
  <div class="field" style="top:252px;padding-bottom:29px">Messages</div>
  <span class="btn">SUBMIT</span>
</form>

<footer class="abs footer">
  <div class="brand"><span class="dot"></span><span class="name">Copper Fern<br>Services</span></div>
  <p class="tagline">DUCTLESS EXPERTS</p>
  <p class="about-text">Lorem ipsum dolor sit amet, consectetur adipiscing elit, sed do eiusmod tempor incididunt ut labore et dolore magna aliqua</p>
  <div class="social"><span></span><span></span><span></span><span></span></div>
  <div class="fcol" style="left:410px"><h5>QUICKS LINKS</h5><ul><li>Home</li><li>About Us</li><li>Services</li><li>Faq</li><li>Review</li><li>Contact Us</li></ul></div>
  <div class="fcol" style="left:642px"><h5>SERVICES</h5><ul><li>Ductless Installation</li><li>Ductless Maintenance</li><li>Ductless Repairs</li><li>Ductless Warranty</li><li>Heat Pumps</li></ul></div>
  <div class="fcol" style="left:887px"><h5>ADDRESS</h5><ul><li>418 Larkspur Ave. Chicago, IL 60619</li><li>555 014 2286</li><li>info@copperfernservices.com</li></ul></div>
  <p class="copy">Copyright © 2019 Copper Fern Services.<span>|</span>Terms of Use<span>|</span>Privacy Policy</p>
</footer>

</body>
</html>
```